Summit Bodyform Gym Website

We need a website design for our gym.

Summit is the UAE's first calisthenics and parkour gym. The theme under which the gym revolves is that one does not require any machinery to workout as our bodies could be themselves the machinery. The gym is designed to be the more of a social hub rather than an "in-and-out" gym, where people come train, have fun, hang out and socialize for a few hours rather than just train for 60 minutes then leave. The gym is designed to be a big open space with lots of natural sunlight, natural wood and plants all over the place to create a natural and refreshing setting. We also use recycled material throughout the gym and recycle our waste as being green is part of our philosophy. We currently also have some of the world's top and most recognized calisthenics athletes working with us.

We would like our website to reflect all that as well as provide a simple, interactive and fun way for visitors to be able to get class and gym information, check out gym media and contact us for bookings.

Target Market(s)

Ages 15-35

Industry/Entity Type

Fitness

Coding

Coded - Design and coding required

Number of Pages Required

4 page

Font styles to use
Decorative

Colors
0792cd

Requirements
Must have
• Class descriptions
• Gym description
• Class schedules
• Trainer profiles
• Gym philosophy
• Contact Details
Nice to have
• A link to contact us directly for a free first trial class

```html
<!DOCTYPE html>
<html lang="en">
<head>
<meta charset="utf-8">
<title>Summit Bodyform Gym</title>
<link href="https://fonts.googleapis.com/css2?family=Raleway:wght@400;500;600&family=Roboto+Slab:wght@400;700&family=Oswald:wght@700&display=swap" rel="stylesheet">
<style>
:root{
  --blue:#0792cd;
  --blue-band:#1ea3d3;
  --blue-light:#3fb0dc;
  --dark:#222629;
  --darker:#1a1c1e;
  --ink:#333;
  --muted:#777;
  --line:#e2e2e2;
  --white:#fff;
}
*{box-sizing:border-box;margin:0;padding:0}
html,body{width:1200px;height:2203px;overflow:hidden}
body{font-family:'Raleway',sans-serif;color:var(--ink);background:#fff;position:relative}
.wrap{width:934px;margin:0 auto;position:relative}
a{color:inherit;text-decoration:none}

.topbar{height:30px;border-bottom:1px solid var(--line);font-size:11px;color:#888}
.topbar .wrap{display:flex;justify-content:space-between;align-items:center;height:30px}
.topbar .pin{color:var(--blue)}
.socials-mini{display:flex;gap:9px}
.socials-mini span{width:8px;height:8px;background:#999;border-radius:2px}

.header{height:132px}
.header .wrap{display:flex;justify-content:space-between;align-items:center;height:132px}
.brand{font-family:'Roboto Slab',serif;font-weight:700;font-size:26px;color:var(--ink)}
.contacts{display:flex;gap:26px}
.contact{display:flex;align-items:center;gap:10px;font-size:11px;line-height:1.7;color:var(--ink)}
.contact .ic{width:36px;height:36px;background:var(--blue);display:flex;align-items:center;justify-content:center}

.nav{height:44px;background:var(--blue);border-top:2px solid #66c4e6;border-bottom:2px solid #66c4e6}
.nav ul{list-style:none;display:flex;height:40px;align-items:stretch}
.nav li{font-size:11.5px;color:#fff;text-transform:uppercase;padding:0 19px;display:flex;align-items:center}
.nav li.active{background:#222;padding:0 31px}

.hero{height:436px;position:relative}
.hero-photo{position:absolute;inset:0;background:
  radial-gradient(ellipse at 50% 35%,rgba(120,110,95,.55),transparent 60%),
  linear-gradient(90deg,#2a2b28 0%,#3c3a34 30%,#4a463d 55%,#3a4034 80%,#2e3430 100%)}
.hero h1{position:absolute;top:180px;width:100%;text-align:center;font-family:'Oswald',sans-serif;font-weight:700;font-size:38px;color:#fff;letter-spacing:.3px;text-transform:uppercase}
.arrow{position:absolute;top:196px;width:40px;height:40px;background:rgba(0,0,0,.35);display:flex;align-items:center;justify-content:center}
.arrow.l{left:22px}.arrow.r{right:22px}

.welcome-band{height:372px;background:var(--blue);position:relative}
.welcome-box{position:absolute;top:-94px;left:133px;width:934px;height:220px;background:var(--blue);text-align:center;padding:30px 78px 0;color:#fff;box-shadow:0 8px 14px rgba(0,0,0,.12)}
.sec-title{font-family:'Roboto Slab',serif;font-weight:700;font-size:23px;letter-spacing:.5px;text-transform:uppercase}
.sec-title::before,.sec-title::after{content:"";display:inline-block;width:8px;height:8px;border-radius:50%;background:currentColor;vertical-align:middle;margin:0 18px}
.sub{font-size:17px;margin:10px 0 22px}
.body-text{font-size:11px;line-height:21px}
.cols{position:absolute;top:134px;left:133px;width:934px;display:flex;color:#fff}
.col{flex:1;padding:0 14px}
.col+.col{border-left:1px solid rgba(255,255,255,.25);padding-left:50px}
.col h3{font-weight:500;font-size:17px;text-transform:uppercase;margin-bottom:10px}
.col p{font-size:11px;line-height:21.5px;color:#e8f5fb}
.btn-dark{display:inline-flex;align-items:center;gap:8px;background:#2b2b2b;color:#fff;font-size:11px;text-transform:uppercase;padding:0 26px;height:36px;margin-top:22px}
.btn-dark i,.btn-blue i,.cta-btn i{width:10px;height:10px;border-radius:50%;background:#fff;display:inline-block}

.schedules{height:708px;position:relative;color:#fff;text-align:center;padding-top:52px}
.schedules-photo{position:absolute;inset:0;background:
  radial-gradient(ellipse at 30% 55%,rgba(60,110,150,.45),transparent 55%),
  linear-gradient(180deg,#26292d,#3a4652 45%,#2a2f35)}
.schedules-content{position:relative}
.schedules .body-text{width:800px;margin:0 auto}
.btn-blue{display:inline-flex;align-items:center;gap:8px;background:var(--blue);color:#fff;font-size:11px;text-transform:uppercase;padding:0 26px;height:36px;margin-top:22px}
.trainer{position:absolute;top:286px;left:133px;width:934px;height:316px;background:#fff;display:flex;text-align:left;color:var(--ink)}
.trainer .photo{width:253px;height:316px;background:
  radial-gradient(ellipse at 50% 30%,#e8a890 0%,rgba(232,168,144,0) 40%),
  radial-gradient(ellipse at 50% 80%,#c9987e 0%,rgba(201,152,126,0) 35%),
  linear-gradient(160deg,#a9a9a7,#7c7a78 55%,#4a4848)}
.trainer .info{padding:30px 44px 0 32px;flex:1}
.trainer h2{font-family:'Roboto Slab',serif;font-weight:700;font-size:23px;color:var(--blue);text-transform:uppercase}
.trainer h4{font-family:'Roboto Slab',serif;font-weight:400;font-size:17px;margin:14px 0 12px;text-transform:uppercase}
.trainer p{font-size:11px;line-height:21.5px;color:var(--muted)}
.follow{display:flex;align-items:center;gap:9px;margin-top:14px;font-size:11px}
.follow span.c{width:35px;height:35px;border-radius:50%}
.dots{position:absolute;top:640px;width:100%;display:flex;justify-content:center;gap:6px}
.dots span{width:8px;height:8px;border-radius:50%;background:var(--blue)}
.dots span.on{background:#fff}

.cta{height:122px;background:var(--blue-band)}
.cta .wrap{display:flex;align-items:center;height:122px;padding-left:108px;gap:106px}
.cta h2{font-family:'Roboto Slab',serif;font-weight:700;font-size:35px;color:#fff}
.cta-btn{display:inline-flex;align-items:center;gap:14px;background:#1d2a30;color:#fff;font-size:18px;text-transform:uppercase;padding:0 32px;height:52px;border:1px solid #0d1518}

.philosophy{height:313px;background:#f4f4f4;padding-top:22px}
.phil-card{width:934px;margin:0 auto;height:258px;background:#fff;display:flex;box-shadow:0 10px 12px -6px rgba(0,0,0,.25)}
.phil-brand{width:330px;display:flex;align-items:center;justify-content:center;font-family:'Roboto Slab',serif;font-weight:700;font-size:34px;color:var(--ink)}
.phil-text{flex:1;border-left:2px solid var(--blue);margin:10px 0;padding:8px 24px 0 26px}
.phil-text h2{font-family:'Roboto Slab',serif;font-weight:700;font-size:23px;color:var(--blue);text-transform:uppercase;margin-bottom:10px}
.phil-text p{font-size:11px;line-height:19px;color:var(--muted)}
.phil-text .btn-blue{margin-top:16px}

.footer{height:46px;background:var(--darker);color:#ddd;font-size:11px}
.footer .wrap{display:flex;justify-content:space-between;align-items:center;height:46px}
.footer nav{display:flex;gap:19px}
.totop{position:absolute;right:14px;bottom:50px;width:40px;height:40px;border-radius:50%;background:var(--blue);border:3px solid #fff;display:flex;align-items:center;justify-content:center}
</style>
</head>
<body>

<div class="topbar"><div class="wrap">
  <span><span class="pin">&#9679;</span> 27, 402 street, Cedar District, Dubai, United Arab Emirates</span>
  <span class="socials-mini"><span></span><span></span><span></span><span></span></span>
</div></div>

<header class="header"><div class="wrap">
  <div class="brand">Summit Bodyform Gym</div>
  <div class="contacts">
    <div class="contact"><span class="ic"><svg width="16" height="18" viewBox="0 0 16 18"><rect x="5" y="1" width="6" height="10" rx="3" fill="#fff"/><path d="M2 8a6 6 0 0012 0M8 14v3" stroke="#fff" stroke-width="1.6" fill="none"/></svg></span><span>Call us on<br>+ 971405550142</span></div>
    <div class="contact"><span class="ic"><svg width="18" height="14" viewBox="0 0 18 14"><rect x="1" y="1" width="16" height="12" fill="#fff"/><path d="M1 1l8 6 8-6" stroke="#0792cd" stroke-width="1.5" fill="none"/></svg></span><span>Email us<br>info@summitbodyform.com</span></div>
    <div class="contact"><span class="ic"><svg width="18" height="18" viewBox="0 0 18 18"><circle cx="9" cy="9" r="7.5" stroke="#fff" stroke-width="1.6" fill="none"/><path d="M9 4.5V9h3.5" stroke="#fff" stroke-width="1.6" fill="none"/></svg></span><span>Sunday - thursday<br>07.00 - 21.00</span></div>
  </div>
</div></header>

<nav class="nav"><div class="wrap"><ul>
  <li class="active">Home</li><li>Class descriptions</li><li>Gym description</li><li>Class schedules</li><li>Trainer profiles</li><li>Gym philosophy</li><li>Contact</li>
</ul></div></nav>

<section class="hero">
  <div class="hero-photo" role="img" aria-label="Photo of an athlete training on bars inside the gym, with plants, rigs and hanging shirts"></div>
  <span class="arrow l"><svg width="10" height="14"><path d="M8 1L2 7l6 6" stroke="#3fb0dc" stroke-width="2" fill="none"/></svg></span>
  <h1>UAE's first calisthenics and parkour gym</h1>
  <span class="arrow r"><svg width="10" height="14"><path d="M2 1l6 6-6 6" stroke="#3fb0dc" stroke-width="2" fill="none"/></svg></span>
</section>

<section class="welcome-band">
  <div class="welcome-box">
    <h2 class="sec-title">Welcome to Summit</h2>
    <p class="sub">Calisthenics gym</p>
    <p class="body-text">The gym is a little tricky to find, but the potted plants hanging off thick sticks of bamboo outside the entrance make it visible from the service road. Inside, the 7,500 square foot gym has an industrial look and feel. It's well-lit and bright, with a host of free weights, rigs and boxes for members to jump and run off. Summit is the antithesis of big franchise gyms. There are no rows of treadmills, cross trainers or complicated-looking weights machines. It is a pared down yet stylish playground for those who want to improve their body strength and develop the techniques of parkour.</p>
  </div>
  <div class="cols">
    <div class="col">
      <h3>Class descriptions</h3>
      <p>Lorem ipsum dolor sit amet, consectetur adipiscing elit. Nullam ac lobortis turpis. Fusce ultrices odio nisi, nec suscipit elit finibus eu. Praesent quis purus ut libero mattis elementum. Pellentesque ultrices varius ante. Duis ac justo vitae lorem elementum gravida eleifend sed quam. Maecenas sed tincidunt augue. Nunc eget rhoncus lacus.</p>
      <a class="btn-dark" href="#">Know more <i></i></a>
    </div>
    <div class="col">
      <h3>Gym descriptions</h3>
      <p>Lorem ipsum dolor sit amet, consectetur adipiscing elit. Nullam ac lobortis turpis. Fusce ultrices odio nisi, nec suscipit elit finibus eu. Praesent quis purus ut libero mattis elementum. Pellentesque ultrices varius ante. Duis ac justo vitae lorem elementum gravida eleifend sed quam. Maecenas sed tincidunt augue. Nunc eget rhoncus lacus.</p>
      <a class="btn-dark" href="#">Know more <i></i></a>
    </div>
  </div>
</section>

<section class="schedules">
  <div class="schedules-photo" role="img" aria-label="Blurred photo of the gym interior with members training"></div>
  <div class="schedules-content">
    <h2 class="sec-title">Class schedules</h2>
    <p class="sub">World Class Trainers With Proven Results</p>
    <p class="body-text">Lorem ipsum dolor sit amet, consectetur adipiscing elit. Nullam ac lobortis turpis. Fusce ultrices odio nisi, nec suscipit elit finibus eu. Praesent quis purus ut libero mattis elementum. Pellentesque ultrices varius ante. Duis ac justo vitae lorem elementum gravida eleifend sed quam. Maecenas sed tincidunt augue. Nunc eget rhoncus lacus.</p>
    <a class="btn-blue" href="#">Know more <i></i></a>
  </div>

  <div class="trainer">
    <div class="photo" role="img" aria-label="Portrait photo of trainer Lena Hart in a peach hooded jacket and sports top"></div>
    <div class="info">
      <h2>Meet your trainer</h2>
      <h4>Lena Hart</h4>
      <p>Lena Hart, takes us through the basic exercises such as shoulder rolls into standing position, which she makes look effortless, but once you get on the floor and try it yourself, it's deceptively difficult. Omar Reyes also teaches classes at Summit and he shows us how to 'skin the cat', a move that we last did when we were about eight years old in the playground hanging off the railings and rolling back with legs crossed above our head – but attempting it again a few decades on, that swing doesn't come so easily. In fact, it doesn't come at all. So we move onto the monkey bars to do some core strength building and pull-ups.</p>
      <div class="follow">Follow with :
        <span class="c" style="background:#1da1f2"></span><span class="c" style="background:#3b5998"></span><span class="c" style="background:#0077b5"></span><span class="c" style="background:#3f5f7a"></span><span class="c" style="background:#dd4b39"></span>
      </div>
    </div>
  </div>
  <div class="dots"><span></span><span class="on"></span><span></span></div>
</section>

<section class="cta"><div class="wrap">
  <h2>Free First Trial Class</h2>
  <a class="cta-btn" href="#">Get started now <i></i></a>
</div></section>

<section class="philosophy">
  <div class="phil-card">
    <div class="phil-brand">Summit</div>
    <div class="phil-text">
      <h2>Gym philosophy</h2>
      <p>Lellentesque quis ipsum eu arcu finibus viverra vel vel mauris. Interdum et malesuada fames ac ante ipsum primis in faucibus. Ut vel ornare lorem, nec euismod libero. Quisque id pulvinar ligula. Duis pharetra massa sed lectus convallis ullamcorper. Praesent lacinia enim a nisi condimentum condimentum. In vel vehicula ex, nec lacinia odio. Proin a libero sodales tortor rutrum accumsan. Cras vestibulum ornare diam, in gravida nisl finibus non. Fusce nisl erat, commodo ut neque nec, euismod congue elit. Praesent sed tellus sed velit pulvinar egestas vel a eros. Quisque feugiat lorem diam, quis posuere erat bibendum rutrum.</p>
      <a class="btn-blue" href="#">More info <i></i></a>
    </div>
  </div>
</section>

<footer class="footer"><div class="wrap">
  <span>Copyright © 2015 Summit</span>
  <nav><a>Home</a><a>Class descriptions</a><a>Gym description</a><a>Class schedules</a><a>Trainer profiles</a><a>Gym philosophy</a><a>Contact</a></nav>
</div></footer>

<a class="totop" href="#"><svg width="14" height="10"><path d="M1 9l6-6 6 6" stroke="#fff" stroke-width="2.4" fill="none"/></svg></a>

</body>
</html>
```